Energy Drink label Valtoro

Design a Label to be used on the packaging label/mock up for a energy drink. The name VALTORO means Black Bull & Bull ( in the 11 languages in the target country we want to launch ). I would like a in your face energy drink label design. Please see uploaded files as reference . Something out of the box thinking. For 500ml tin can label.

Target Market(s)

Population of Africa

Industry/Entity Type

Energy Drink

Colors
EB3D1F
EC4F4E
F09395
F8D3D4
FCEDEE

Requirements
Must have
• Bold and attractive design ( Black , Red , Silver , White ) as MAIN color scheme, as attached files I uploaded
Nice to have
• option of a white background and also black ( matte / carbon fibre effect )

```html
<!DOCTYPE html>
<html lang="en">
<head>
<meta charset="utf-8">
<title>Valtoro Energy Drink – Can Label</title>
<link rel="stylesheet" href="https://fonts.googleapis.com/css2?family=Teko:wght@500;600;700&family=Oswald:wght@400;500&display=swap">
<style>
  :root {
    --label-black: #0b0b0c;
    --label-deep-red: #5a0b10;
    --brand-red: #d8242f;
    --brand-red-bright: #ec4f4e;
    --brand-red-dark: #8c121a;
    --label-white: #ffffff;
    --label-silver: #c9ccd1;
  }
  * { margin: 0; padding: 0; box-sizing: border-box; }
  html, body {
    width: 1177px; height: 1200px; overflow: hidden;
    background: #ffffff;
  }
  .can-label {
    position: relative;
    width: 1177px; height: 1200px;
    overflow: hidden;
    background:
      linear-gradient(90deg, transparent 0 8%, rgba(140,18,26,.45) 10%, transparent 13% 30%, rgba(140,18,26,.35) 33%, transparent 37% 58%, rgba(140,18,26,.4) 62%, transparent 66% 84%, rgba(140,18,26,.35) 88%, transparent 92%),
      var(--label-black);
    font-family: "Oswald", sans-serif;
    color: var(--label-white);
  }
  .bottom-band {
    position: absolute; left: 0; bottom: 0;
    width: 1177px; height: 420px;
  }
  .wordmark {
    position: absolute;
    left: 70px; top: 40px;
    height: 1120px;
    writing-mode: vertical-rl;
    transform: rotate(180deg);
    font-family: "Teko", sans-serif;
    font-weight: 700;
    font-size: 300px;
    line-height: 0.82;
    letter-spacing: 4px;
    text-align: center;
    color: var(--label-white);
  }
  .product-type {
    position: absolute;
    left: 345px; top: 360px;
    height: 640px;
    writing-mode: vertical-rl;
    transform: rotate(180deg);
    font-family: "Teko", sans-serif;
    font-weight: 700;
    font-size: 96px;
    line-height: 1;
    letter-spacing: 6px;
    color: var(--brand-red);
    text-align: center;
  }
  .tagline {
    position: absolute;
    left: 450px; top: 300px;
    height: 700px;
    writing-mode: vertical-rl;
    transform: rotate(180deg);
    font-family: "Oswald", sans-serif;
    font-weight: 400;
    font-size: 34px;
    letter-spacing: 2px;
    text-align: center;
    color: var(--label-white);
    border-right: 3px solid var(--brand-red);
    padding-right: 8px;
  }
  .emblem-area {
    position: absolute;
    left: 560px; top: 90px;
    width: 440px; height: 440px;
    border-radius: 50%;
    background: radial-gradient(circle at 45% 40%, var(--brand-red) 0%, var(--brand-red-dark) 55%, #2a2a2e 100%);
  }
  .facts {
    position: absolute;
    left: 640px; top: 600px;
    width: 380px;
    list-style: none;
  }
  .fact {
    padding: 10px 0 14px;
    border-bottom: 3px solid var(--brand-red);
    font-family: "Teko", sans-serif;
    line-height: 0.85;
  }
  .fact:last-child { border-bottom: none; }
  .fact-value {
    display: block;
    font-weight: 600;
    font-size: 104px;
  }
  .fact-label {
    display: block;
    font-weight: 500;
    font-size: 52px;
    letter-spacing: 1px;
  }
</style>
</head>
<body>
  <main class="can-label">
    <svg class="bottom-band" viewBox="0 0 1177 420" preserveAspectRatio="none" aria-hidden="true">
      <defs>
        <linearGradient id="bandFill" x1="0" y1="0" x2="0" y2="1">
          <stop offset="0" stop-color="#d8242f"/>
          <stop offset="1" stop-color="#8c121a"/>
        </linearGradient>
      </defs>
      <path d="M0 130 C 300 260, 700 330, 1177 90 L1177 420 L0 420 Z" fill="url(#bandFill)"/>
    </svg>

    <h1 class="wordmark">VALTORO</h1>
    <p class="product-type">ENERGY DRINK</p>
    <p class="tagline">REFUEL / REHYDRATE / RE-ENERGIZE</p>

    <div class="emblem-area" role="img" aria-label="Brand emblem area"></div>

    <ul class="facts">
      <li class="fact"><span class="fact-value">50</span><span class="fact-label">CALORIES</span></li>
      <li class="fact"><span class="fact-value">70 G</span><span class="fact-label">CAFFEINE</span></li>
      <li class="fact"><span class="fact-value">500 ML</span><span class="fact-label">NET CONTENT</span></li>
    </ul>
  </main>
</body>
</html>
```